Stylish business cards for KV7

To create an appealing and professional business card design for a WOMEN Owned Construction Supply Company.
2 sided card. Incorporate brand elements, curvy, colorful, sleek and bright. No solid white background. attached samples of styles added shapes/ribbons. Want something with that WOW that looks awesome, factor. It is a new logo, so feel free to mess with logo colors in the blue and teal factors that can look good with both dark and light background. If you want to try a watermark with just the KV7, without the "Supply" that might look cool to.

Industry/Entity Type

Women owned construction supply company

Contact Information for Business Card

Name, Title, and phone number and email, web page. maybe spot for qr code.

Font styles to use
Sans Serif

Requirements
Nice to have
• would love to see colors, maybe stylish ribbon dividers or some sort of 2 or 3 tone color card that compliments logo.
Should not have
• Please do not have all white background. Do not include Home/reale state/ or building images.

```html
<!DOCTYPE html>
<html lang="en">
<head>
<meta charset="utf-8">
<title>KV7 Supply – Business Cards</title>
<link rel="stylesheet" href="https://fonts.googleapis.com/css2?family=Montserrat:wght@400;500;600;700&display=swap">
<style>
  :root {
    --stage: #1b1b1d;
    --navy: #1b3858;
    --navy-deep: #16304d;
    --teal: #2193b6;
    --white: #f4f5f6;
  }
  * { margin: 0; padding: 0; box-sizing: border-box; }
  html, body {
    width: 1200px; height: 1059px; overflow: hidden;
    background: var(--stage);
    font-family: "Montserrat", sans-serif;
  }
  .canvas { position: relative; width: 1200px; height: 1059px; }
  .card {
    position: absolute; left: 255px; width: 690px; height: 390px;
    border-radius: 18px; overflow: hidden; background: var(--navy);
  }
  .card--front { top: 89px; }
  .card--back { top: 547px; }
  .card__band { position: absolute; inset: 0; width: 100%; height: 100%; }
  .brand-name {
    position: absolute; color: var(--white); font-weight: 600;
    white-space: nowrap; letter-spacing: 0.5px;
  }
  .card--front .brand-name { left: 35px; top: 62px; font-size: 40px; }
  .card--back .brand-name { left: 300px; top: 172px; font-size: 56px; }
  .identity__marker {
    position: absolute; left: 0; top: 205px; width: 18px; height: 35px;
    background: var(--teal);
  }
  .identity__name {
    position: absolute; left: 35px; top: 200px;
    font-size: 21px; font-weight: 700; color: var(--teal); letter-spacing: 0.3px;
  }
  .identity__title {
    position: absolute; left: 35px; top: 226px;
    font-size: 14px; font-weight: 500; color: var(--white);
  }
  .contact { position: absolute; left: 35px; top: 266px; list-style: none; }
  .contact__item {
    display: flex; align-items: center; height: 24.3px;
    font-size: 14.5px; font-weight: 500; color: var(--white);
  }
  .contact__icon { width: 13px; height: 13px; margin-right: 7px; flex: none; fill: var(--teal); }
</style>
</head>
<body>
<main class="canvas">

  <section class="card card--front" aria-label="Business card front">
    <svg class="card__band" viewBox="0 0 690 390" aria-hidden="true">
      <circle cx="930" cy="195" r="360" fill="var(--teal)"/>
      <circle cx="930" cy="195" r="325" fill="none" stroke="var(--white)" stroke-width="12"/>
      <circle cx="930" cy="195" r="300" fill="none" stroke="var(--navy-deep)" stroke-width="4"/>
    </svg>
    <div class="brand-name">KV7 Supply</div>
    <span class="identity__marker"></span>
    <h1 class="identity__name">DANA WHITLEY</h1>
    <p class="identity__title">CEO/Founder</p>
    <ul class="contact">
      <li class="contact__item">
        <svg class="contact__icon" viewBox="0 0 16 16"><path d="M3.6 1.2l2.3 2.9-1.3 1.7c.9 2 2.6 3.8 4.7 4.8l1.7-1.3 2.9 2.3-1.4 2.2C7.2 13.6 2.5 8.9 1.3 2.6z"/></svg>
        555.214.0387
      </li>
      <li class="contact__item">
        <svg class="contact__icon" viewBox="0 0 16 16"><path d="M1 3h14v10H1z" fill="none" stroke="var(--teal)" stroke-width="1.6"/><path d="M1 3l7 6 7-6" fill="none" stroke="var(--teal)" stroke-width="1.6"/></svg>
        info@kv7supply.com.au
      </li>
      <li class="contact__item">
        <svg class="contact__icon" viewBox="0 0 16 16"><g fill="none" stroke="var(--teal)" stroke-width="1.3"><circle cx="8" cy="8" r="6.5"/><ellipse cx="8" cy="8" rx="3" ry="6.5"/><path d="M1.5 8h13M2.5 4.7h11M2.5 11.3h11"/></g></svg>
        www.kv7supply.com.au
      </li>
      <li class="contact__item">
        <svg class="contact__icon" viewBox="0 0 16 16"><path d="M8 0.5a5.3 5.3 0 0 0-5.3 5.3C2.7 10 8 15.5 8 15.5s5.3-5.5 5.3-9.7A5.3 5.3 0 0 0 8 .5zm0 7.4a2.1 2.1 0 1 1 0-4.2 2.1 2.1 0 0 1 0 4.2z"/></svg>
        P.O Box 4127 Harbour Road Westbay CD 20417
      </li>
    </ul>
  </section>

  <section class="card card--back" aria-label="Business card back">
    <svg class="card__band" viewBox="0 0 690 390" aria-hidden="true">
      <circle cx="-260" cy="195" r="470" fill="var(--teal)"/>
      <circle cx="-260" cy="195" r="430" fill="none" stroke="var(--white)" stroke-width="12"/>
    </svg>
    <div class="brand-name">KV7 Supply</div>
  </section>

</main>
</body>
</html>
```